Business Card for Multi-Brand Sportswear Company

We are looking for a business card which represents our company and the multiple brands within it.

The company: Fen Athletics (LTD)
The brands: Fen, TavaPuni, ElmStretch, Grit and Rain

Employees using these cards would be representing Fen Athletics, rather than any of the individual brands. You will see a current design within the uploaded files, to give some inspiration. The actual text of the brands is not necessary, but the logos should be on there is some format.

Our creative minds on this are stretched, so we are looking for someone to make this their own, and show us what a good business card should look like.

We may like to get these printed with spot gloss, so keep that in mind with your designs.

www.fenathletics.co.uk

Industry/Entity Type

Business

Contact Information for Business Card

Leo Pemberton-Hale
Operations Manager
(+44) 1632 960 418
Leo@fenathletics.co.uk
www.fenathletics.co.uk

Font styles to use
Sans Serif
Other font styles liked:
• Eurostile

Colors
ffffff

Requirements
Nice to have
• Dark (black) background

```html
<!DOCTYPE html>
<html lang="en">
<head>
<meta charset="utf-8">
<title>Fen Athletics – Business Card</title>
<link href="https://fonts.googleapis.com/css2?family=Ubuntu:ital,wght@0,400;0,500;0,700;1,400&display=swap" rel="stylesheet">
<style>
  :root {
    --backdrop: #3b3b3b;
    --card-white: #ffffff;
    --card-black: #000000;
    --ink: #1a1a1a;
    --ink-soft: #555555;
    --brand-red: #e41e26;
    --brand-grey: #8a8a8a;
    --brand-plum: #5e4f63;
    --paper-text: #ffffff;
  }
  * { box-sizing: border-box; margin: 0; padding: 0; }
  html, body {
    width: 1105px; height: 1200px; overflow: hidden;
    background: var(--backdrop);
    font-family: "Ubuntu", "Helvetica Neue", Arial, sans-serif;
  }
  .card {
    position: absolute; left: 196px; width: 720px; height: 412px;
    overflow: hidden;
  }
  .card--front { top: 146px; background: var(--card-white); }
  .card--back { top: 602px; background: var(--card-black); }

  .wordmark {
    position: absolute; left: 47px; top: 78px;
    display: flex; align-items: center; gap: 12px;
    font-weight: 700; font-size: 34px; letter-spacing: 0.01em;
    color: var(--ink);
  }
  .wordmark__dot {
    width: 16px; height: 16px; border-radius: 50%;
    background: var(--brand-red);
  }

  .contact {
    position: absolute; left: 47px; top: 230px;
    font-size: 18px; line-height: 25px; color: var(--ink-soft);
  }
  .contact__address { margin-bottom: 8px; }
  .contact__line { display: flex; align-items: center; gap: 10px; line-height: 29px; }
  .contact__icon { width: 16px; height: 16px; flex: none; }

  .holder {
    position: absolute; right: 47px; top: 254px; text-align: right;
  }
  .holder__name {
    font-weight: 500; font-size: 25px; color: var(--brand-red); line-height: 32px;
  }
  .holder__role { font-size: 19px; color: var(--ink); line-height: 26px; }

  .web-band {
    position: absolute; right: 0; bottom: 0; width: 352px; height: 50px;
  }
  .web-band svg { position: absolute; inset: 0; }
  .web-band__url {
    position: absolute; right: 39px; top: 13px;
    font-size: 18px; letter-spacing: 0.09em; color: var(--paper-text);
  }

  .brand-row {
    position: absolute; left: 0; right: 0; top: 186px;
    display: flex; justify-content: center; align-items: center; gap: 34px;
    font-weight: 700; font-size: 28px;
  }
  .brand-row__item { display: flex; align-items: center; gap: 9px; }
  .brand-row__item--fen { color: var(--paper-text); }
  .brand-row__item--tava { color: var(--brand-grey); }
  .brand-row__item--elm { color: #8c7b91; }
  .brand-row__item--grit { color: var(--brand-red); }
  .brand-row__square {
    width: 18px; height: 18px; background: var(--brand-plum); border-radius: 3px;
  }
  .back-url {
    position: absolute; left: 0; right: 0; top: 336px; text-align: center;
    font-style: italic; font-size: 19px; letter-spacing: 0.5em; color: var(--paper-text);
  }
</style>
</head>
<body>
  <section class="card card--front" aria-label="Card front">
    <div class="wordmark"><span class="wordmark__dot"></span>Fen Athletics</div>

    <div class="contact">
      <p class="contact__address">Alder Court, Hollins<br>Ashby, ZZ9 4QT</p>
      <p class="contact__line">
        <svg class="contact__icon" viewBox="0 0 16 16" aria-hidden="true">
          <path fill="#e41e26" d="M3.6 1.2l2.3 2.6-1.4 1.9c.9 2.1 3.1 4.6 5.8 5.8l1.9-1.4 2.6 2.3-1.5 2.4C7.4 14.7 1.3 8.6.9 2.7z"/>
        </svg>
        +44 (0)1632 960418
      </p>
      <p class="contact__line">
        <svg class="contact__icon" viewBox="0 0 16 16" aria-hidden="true">
          <rect x="1" y="3.5" width="14" height="9.5" fill="#e41e26"/>
          <path d="M1.5 4l6.5 5 6.5-5" fill="none" stroke="#ffffff" stroke-width="1.3"/>
        </svg>
        leo@fenathletics.co.uk
      </p>
    </div>

    <div class="holder">
      <p class="holder__name">Leo Pemberton-Hale</p>
      <p class="holder__role">Operations Manager</p>
    </div>

    <div class="web-band">
      <svg viewBox="0 0 352 50" preserveAspectRatio="none" aria-hidden="true">
        <path d="M0 50 C20 34 30 6 70 0 L352 0 L352 50 Z" fill="#e41e26"/>
      </svg>
      <span class="web-band__url">www.fenathletics.co.uk</span>
    </div>
  </section>

  <section class="card card--back" aria-label="Card back">
    <div class="brand-row">
      <span class="brand-row__item brand-row__item--fen">Fen</span>
      <span class="brand-row__item brand-row__item--tava">TavaPuni</span>
      <span class="brand-row__item brand-row__item--elm"><span class="brand-row__square"></span>ElmStretch</span>
      <span class="brand-row__item brand-row__item--grit">Grit and Rain</span>
    </div>
    <p class="back-url">www.fenathletics.co.uk</p>
  </section>
</body>
</html>
```